Larkmoor Drones Business Card

We are a new company based in Central Queensland, Australia that uses specalised drones (Voskel Ferra Q80) to undertake mainly agricultural operations, like spraying weeds, spraying crops, spreading seed etc. I have attached a Plimbo proof of a card I was thinking along the lines of - purely a start point. The drone used in the business card MUST be a Voskel Ferra Q80.
I am very open to other ideas, especially fonts and layout. I don't have website etc set up yet.
The images are stock and easily interchangeable, I just ask that any background images reflect the local central Queensland area. The photo of the drone is not even complete (propellers cut off) and I need a new stock photo – I’m not sure if this is an issue, or I can pay for an image if need be. PLEASE FIND AN FERRA Q80 image - 4 sprayers, not 6.
The logo/business name is very draft and looking for further ideas, ideally incorporating drones or agriculture design elements into the design of the business name. The business name needs work on the graphic/design – it is a draft that I have included, the drone propellers (being a different colour) are DRAFT only and intended for changes. PLEASE DO NOT USE THE DRONE PORPELLER I HAVE USED AS A DRAFT. TRY TO FIND SOMETHING ELSE.. The arrow is a shape and not aligned in any way, I would also like ideas on different fonts and additional elements, like air streams, aviation elements, aviation or country western (farming like) themes and fonts etc.
Ideally looking at staying within the blue, green and yellow colours, keeping with an natural, outdoorsy, environmental feel.

Target Market(s)

Farmers, Agriculture, Local Governments, Land Managers

Industry/Entity Type

Agriculture, Drones, Aviation

Contact Information for Business Card

Agricultural Drone (Voskel Ferra Q80), Farming, Business Name.

Font styles to use
Sans Serif

Colors
0054AA
0677BA
7BADD7
CADEEF
E8F1F8
0094D4
00A9DD
6FCCEA
C7EBF8
E9F6FB
00AB8E
00BBA5
67D7C9
C6EFE9
E9F9F6
59FF00
82FF00
B8FF75
E3FFCB
F4FFEA

Requirements
Must have
• Voskel Ferra Q80 Drone
Should not have
• Tractors

```html
<!DOCTYPE html>
<html lang="en">
<head>
<meta charset="utf-8">
<title>Larkmoor Drones – Business Card</title>
<link href="https://fonts.googleapis.com/css2?family=Marcellus&family=Montserrat:wght@500;700&family=Crimson+Text:wght@700&display=swap" rel="stylesheet">
<style>
  :root {
    --stage: #dcdcdc;
    --edge-green: #59ff00;
    --sky-teal: #67b7a8;
    --sky-blue: #7badd7;
    --sky-pale: #e8f1f8;
    --grass-light: #8cc63f;
    --grass-deep: #3f7d1c;
    --horizon: #a9c77e;
    --drone-grey: #5b6466;
    --spray-mist: #e6dcb4;
    --ink-white: #ffffff;
    --accent-yellow: #f2e600;
  }
  * { margin: 0; padding: 0; box-sizing: border-box; }
  html, body { width: 1200px; height: 800px; overflow: hidden; }
  body {
    background: var(--stage);
    position: relative;
    font-family: "Montserrat", Arial, sans-serif;
  }
  .card {
    position: absolute;
    top: 235px;
    width: 540px;
    height: 330px;
    border-radius: 18px;
    overflow: hidden;
    border: 2px solid var(--edge-green);
    color: var(--ink-white);
  }
  .card--contact { left: 40px; }
  .card--brand { left: 620px; }

  .photo { position: absolute; inset: 0; }
  .photo--field-teal {
    background: linear-gradient(180deg, var(--sky-teal) 0%, #9fd3b8 30%, #cfe8b0 48%, var(--horizon) 55%, var(--grass-light) 70%, var(--grass-deep) 100%);
  }
  .photo--field-sky {
    background: linear-gradient(180deg, var(--sky-blue) 0%, #b7d2ea 28%, var(--sky-pale) 48%, #d9e3c4 56%, var(--grass-light) 70%, var(--grass-deep) 100%);
  }

  .drone-photo {
    position: absolute;
    border-radius: 50%;
    background: radial-gradient(ellipse at 50% 40%, rgba(91,100,102,0.55) 0%, rgba(91,100,102,0.25) 40%, rgba(230,220,180,0.35) 65%, rgba(230,220,180,0) 100%);
  }
  .card--contact .drone-photo { left: 290px; top: 118px; width: 170px; height: 100px; }
  .card--brand .drone-photo { left: 170px; top: 150px; width: 220px; height: 120px; }

  .wordmark {
    position: absolute;
    font-family: "Marcellus", Georgia, serif;
    font-weight: 400;
    color: var(--ink-white);
    line-height: 0.95;
    letter-spacing: 1px;
    white-space: nowrap;
  }
  .card--contact .wordmark { right: 42px; top: 24px; font-size: 42px; }
  .card--contact .wordmark .line2 { padding-left: 58px; display: block; }
  .card--brand .wordmark { left: 150px; top: 46px; font-size: 46px; }
  .card--brand .wordmark .line2 { padding-left: 40px; display: block; }

  .contact {
    position: absolute;
    left: 30px; top: 104px;
    white-space: nowrap;
  }
  .contact__name { font-weight: 700; font-size: 18px; letter-spacing: 0.5px; text-transform: uppercase; line-height: 22px; }
  .contact__role { font-weight: 500; font-size: 13px; margin-bottom: 6px; line-height: 18px; }
  .contact__row {
    display: flex; align-items: center; gap: 8px;
    font-weight: 500; font-size: 13px; line-height: 18px;
  }
  .contact__row svg { width: 12px; height: 12px; flex: none; }

  .tagline {
    position: absolute;
    left: 30px; top: 234px;
    font-family: "Crimson Text", Georgia, serif;
    font-weight: 700;
    font-size: 24px;
    line-height: 28px;
    letter-spacing: 0.5px;
    text-transform: uppercase;
    white-space: nowrap;
  }
  .services {
    position: absolute;
    left: 30px; top: 272px;
    font-family: "Crimson Text", Georgia, serif;
    font-weight: 700;
    font-size: 17px;
    line-height: 22px;
    white-space: nowrap;
    display: flex; align-items: center; gap: 10px;
  }
  .services .dot {
    width: 5px; height: 5px; border-radius: 50%;
    background: var(--accent-yellow);
    flex: none;
  }
</style>
</head>
<body>

  <section class="card card--contact">
    <div class="photo photo--field-teal" role="img" aria-label="Green Central Queensland paddock with a tree line and hills under a teal sky"></div>
    <div class="drone-photo" role="img" aria-label="Voskel Ferra Q80 agricultural drone with four sprayers, spraying mist over the paddock"></div>

    <div class="wordmark"><span>LARKMOOR</span><span class="line2">DRONES</span></div>

    <div class="contact">
      <p class="contact__name">Marcus Ellery</p>
      <p class="contact__role">Managing Director</p>
      <p class="contact__row">
        <svg viewBox="0 0 16 16" fill="none" stroke="#fff" stroke-width="1.8"><path d="M3 2l3 1 1 3-2 1.5a8 8 0 0 0 3.5 3.5L10 9l3 1 1 3-2 1.5C7 14 2 9 1.5 4z"/></svg>
        045-210 387 654
      </p>
      <p class="contact__row">
        <svg viewBox="0 0 16 16" fill="#fff"><path d="M1 3h14v10H1z"/><path d="M1 3l7 6 7-6" fill="none" stroke="#6aa" stroke-width="1.4"/></svg>
        info@larkmoor.net
      </p>
      <p class="contact__row">
        <svg viewBox="0 0 16 16" fill="none" stroke="#fff" stroke-width="1.4"><circle cx="8" cy="8" r="6.5"/><ellipse cx="8" cy="8" rx="3" ry="6.5"/><path d="M1.5 8h13"/></svg>
        www.larkmoor.net
      </p>
    </div>

    <p class="tagline">Servicing Central Queensland</p>
    <p class="services">
      <span>Spraying Weeds</span><span class="dot"></span>
      <span>Spraying Crops</span><span class="dot"></span>
      <span>Spreading Seeds</span>
    </p>
  </section>

  <section class="card card--brand">
    <div class="photo photo--field-sky" role="img" aria-label="Green paddock at sunrise with a tree line and distant hills under a blue sky"></div>
    <div class="drone-photo" role="img" aria-label="Voskel Ferra Q80 agricultural drone with four sprayers, spraying mist over the paddock"></div>
    <div class="wordmark"><span>LARKMOOR</span><span class="line2">DRONES</span></div>
  </section>

</body>
</html>
```